Business Card Design

We need a business card designed for our new company. Prefer a black card with white logo & writing.

Contact Information for Business Card

Ted Galloway, address: 7-4812 Fernhollow Road, Abbotsford, BC, V3K 8R2, Office Phone: 604-712-3390, Cell: 604-947-2164, Email: ted@resinworkshub.ca

Colors

Designer to choose only greyscale colors for use in the design.

```html
<!DOCTYPE html>
<html lang="en">
<head>
<meta charset="UTF-8">
<title>Resinworks Hub – Business Card</title>
<link href="https://fonts.googleapis.com/css2?family=Poppins:wght@300;400;700&display=swap" rel="stylesheet">
<style>
  :root {
    --backdrop: #232323;
    --card: #1e1e20;
    --ink: #ffffff;
    --ink-soft: #e6e6e6;
    --mark-grey: #8c8c8f;
  }
  * { margin: 0; padding: 0; box-sizing: border-box; }
  html, body {
    width: 1200px; height: 780px; overflow: hidden;
    background: var(--backdrop);
    font-family: "Poppins", sans-serif;
    color: var(--ink);
  }
  .stage {
    position: relative; width: 1200px; height: 780px;
    display: flex; align-items: center; justify-content: center; gap: 50px;
  }
  .card {
    position: relative; width: 525px; height: 300px;
    background: var(--card);
    box-shadow: 0 18px 40px rgba(0,0,0,.55);
  }
  /* Front */
  .brand {
    position: absolute; top: 30px; right: 34px;
    display: flex; align-items: center; gap: 8px;
    font-weight: 700; font-size: 22px; letter-spacing: .5px; color: var(--ink);
  }
  .brand-dot { width: 12px; height: 12px; background: var(--ink); }
  .identity {
    position: absolute; left: 34px; bottom: 112px;
    padding-left: 18px;
  }
  .identity::before {
    content: ""; position: absolute; left: 0; top: 6px;
    width: 9px; height: 46px; background: var(--ink);
  }
  .person-name { font-size: 27px; line-height: 1.1; font-weight: 300; }
  .person-name .first { font-weight: 700; }
  .person-title { font-size: 13px; font-weight: 300; color: var(--ink-soft); margin-top: 2px; }
  .address {
    position: absolute; left: 52px; bottom: 70px;
    font-size: 12px; font-weight: 300; line-height: 1.45; color: var(--ink-soft);
  }
  .contacts {
    position: absolute; left: 34px; bottom: -56px; list-style: none;
    font-size: 12px; font-weight: 300; color: var(--ink-soft);
  }
  .contacts li { display: flex; align-items: center; gap: 8px; height: 18px; }
  .contacts svg { width: 12px; height: 12px; fill: var(--ink); flex: none; }
  .front .contacts { bottom: 16px; top: auto; }
  .front .address { bottom: 100px; }
  .front .identity { bottom: 142px; }
  /* Back */
  .back { display: flex; align-items: center; justify-content: center; }
  .back-brand {
    font-weight: 700; font-size: 46px; letter-spacing: 1px; color: var(--mark-grey);
    display: flex; align-items: center; gap: 14px;
  }
  .back-brand .brand-dot { width: 22px; height: 22px; background: var(--mark-grey); }
</style>
</head>
<body>
<main class="stage">
  <section class="card front" aria-label="Card front">
    <div class="brand"><span class="brand-dot"></span>Resinworks Hub</div>

    <div class="identity">
      <h1 class="person-name"><span class="first">Ted</span> Galloway</h1>
      <p class="person-title">Founder &amp; CEO</p>
    </div>

    <p class="address">7-4812 Fernhollow Road,<br>Abbotsford, BC, V3K 8R2.</p>

    <ul class="contacts">
      <li>
        <svg viewBox="0 0 24 24"><path d="M6.6 10.8a15 15 0 0 0 6.6 6.6l2.2-2.2c.3-.3.7-.4 1-.2 1.1.4 2.3.6 3.6.6.6 0 1 .4 1 1V20c0 .6-.4 1-1 1A17 17 0 0 1 3 4c0-.6.4-1 1-1h3.5c.6 0 1 .4 1 1 0 1.3.2 2.5.6 3.6.1.3 0 .7-.2 1z"/></svg>
        604-712-3390
      </li>
      <li>
        <svg viewBox="0 0 24 24"><path d="M7 1h10a2 2 0 0 1 2 2v18a2 2 0 0 1-2 2H7a2 2 0 0 1-2-2V3a2 2 0 0 1 2-2zm0 3v14h10V4zm5 15.5a1 1 0 1 0 0 2 1 1 0 0 0 0-2z"/></svg>
        604-947-2164
      </li>
      <li>
        <svg viewBox="0 0 24 24"><path d="M12 2a10 10 0 1 0 0 20 10 10 0 0 0 0-20zm6.9 6h-3a15 15 0 0 0-1.3-3.9A8 8 0 0 1 18.9 8zM12 4c.8 1.2 1.5 2.5 1.9 4h-3.8c.4-1.5 1.1-2.8 1.9-4zM4.3 14a8 8 0 0 1 0-4h3.4a16 16 0 0 0 0 4zm.8 2h3a15 15 0 0 0 1.3 3.9A8 8 0 0 1 5.1 16zm3-8h-3a8 8 0 0 1 4.3-3.9A15 15 0 0 0 8.1 8zM12 20c-.8-1.2-1.5-2.5-1.9-4h3.8c-.4 1.5-1.1 2.8-1.9 4zm2.3-6H9.7a14 14 0 0 1 0-4h4.6a14 14 0 0 1 0 4zm.3 5.9a15 15 0 0 0 1.3-3.9h3a8 8 0 0 1-4.3 3.9zm1.7-5.9a16 16 0 0 0 0-4h3.4a8 8 0 0 1 0 4z"/></svg>
        www.resinworkshub.ca
      </li>
      <li>
        <svg viewBox="0 0 24 24"><path d="M3 5h18a1 1 0 0 1 1 1v12a1 1 0 0 1-1 1H3a1 1 0 0 1-1-1V6a1 1 0 0 1 1-1zm1 2.4V17h16V7.4l-8 5.3z M5.5 7 12 11.2 18.5 7z"/></svg>
        ted@resinworkshub.ca
      </li>
    </ul>
  </section>

  <section class="card back" aria-label="Card back">
    <div class="back-brand"><span class="brand-dot"></span>Resinworks Hub</div>
  </section>
</main>
</body>
</html>
```